Realty Group Needs Classy, Contemporary Letterhead Design

We need a letterhead design for a new realty company located in NY, USA. We buy investment properties to rehabilitate and or keep in our rental portfolio.

```html
<!DOCTYPE html>
<html lang="en">
<head>
<meta charset="utf-8">
<title>Meridian Realty Group – Letterhead</title>
<link href="https://fonts.googleapis.com/css2?family=Poppins:wght@400;600&family=Questrial&display=swap" rel="stylesheet">
<style>
  :root {
    --brand-purple: #4a2c88;
    --accent-grey: #8b8b8b;
    --paper-light: #efefef;
    --paper-dark: #e1e1e1;
    --ink: #2b2b2b;
    --ink-soft: #3a3a3a;
  }
  * { margin: 0; padding: 0; box-sizing: border-box; }
  html, body { width: 960px; height: 1200px; overflow: hidden; }
  body { background: var(--paper-dark); }
  .letterhead {
    position: relative;
    width: 960px;
    height: 1200px;
    background: linear-gradient(100deg, var(--paper-light) 0%, #e8e8e8 50%, var(--paper-dark) 100%);
    font-family: "Questrial", "Century Gothic", sans-serif;
    color: var(--ink);
  }
  .edge-bar {
    position: absolute; left: 0; top: 0; width: 9px; height: 1200px;
    background: var(--brand-purple);
  }
  .edge-bar__accent {
    position: absolute; left: 0; top: 78px; width: 9px; height: 86px;
    background: var(--accent-grey);
    border-top: 3px solid #fff; border-bottom: 3px solid #fff;
  }
  .brand {
    position: absolute; left: 87px; top: 112px;
    display: flex; align-items: center; gap: 12px;
  }
  .brand__dot {
    width: 22px; height: 22px; border-radius: 50%; background: var(--brand-purple);
  }
  .brand__name {
    font-family: "Poppins", sans-serif; font-weight: 600;
    font-size: 34px; letter-spacing: 0.5px; color: var(--brand-purple);
  }
  .salutation {
    position: absolute; left: 87px; top: 352px;
    font-size: 21px; color: var(--ink);
  }
  .letter-body {
    position: absolute; left: 87px; top: 412px; width: 793px;
    font-size: 13px; line-height: 18.3px; color: var(--ink-soft);
    text-align: justify;
  }
  .letter-body p { margin-bottom: 18.3px; }
  .closing {
    position: absolute; left: 87px; top: 798px;
    font-size: 13px; color: var(--ink-soft);
  }
  .signature {
    position: absolute; left: 87px; top: 842px; width: 126px; height: 68px;
    background: linear-gradient(90deg, #d2d2d2, #c8c8c8);
    border-radius: 4px;
  }
  .footer-rule {
    position: absolute; left: 87px; top: 1084px; width: 793px; height: 1px;
    background: var(--brand-purple);
  }
  .contact {
    position: absolute; top: 1096px;
    font-family: "Poppins", sans-serif; font-size: 14px; line-height: 16.5px; color: var(--ink);
  }
  .contact--left { left: 87px; }
  .contact--right { right: 80px; text-align: right; }
  .contact__row { display: flex; align-items: center; gap: 7px; }
  .contact__row svg { width: 10px; height: 10px; fill: var(--brand-purple); }
  .contact__web { color: var(--brand-purple); font-weight: 600; letter-spacing: 0.6px; }
</style>
</head>
<body>
<main class="letterhead">
  <div class="edge-bar"></div>
  <div class="edge-bar__accent"></div>

  <header class="brand">
    <span class="brand__dot"></span>
    <span class="brand__name">Meridian Realty Group, LLC</span>
  </header>

  <p class="salutation">Dear Mr. Harlow,</p>

  <section class="letter-body">
    <p>Lorem ipsum dolor sit amet, consectetur adipiscing elit. Donec orci purus, luctus vitae dignissim eu, iaculis sed purus. Vivamus faucibus, ipsum nec aliquet viverra, leo mauris condimentum ligula, sit amet sagittis enim ligula quis arcu. Nam egestas tortor id nisi porttitor mattis. In tortor ante, ultricies in suscipit a, tempus non massa. Vivamus et auctor mi. Fusce vel massa nulla. Phasellus nec eros mauris, et scelerisque orci.</p>
    <p>Donec malesuada orci vitae nulla accumsan porta a id massa. Quisque accumsan iaculis magna sit amet fringilla. Maecenas consequat, magna eget tincidunt semper, odio nibh rutrum mi, id feugiat ante nisi eu risus. Vestibulum nunc orci, rhoncus a placerat in, ultricies in mi. Cras mattis varius eros, vel fringilla nisi suscipit eget. Quisque scelerisque sagittis nulla at porttitor.</p>
    <p>Sed id augue vitae urna euismod commodo aliquet a quam. Pellentesque arcu velit, cursus et malesuada ut, consequat et diam. Nullam erat sem, rhoncus id ullamcorper vitae, rhoncus et arcu. In ultricies ultricies nulla, ut rutrum nisi iaculis at. Donec eu magna a metus ornare faucibus. Fusce aliquet faucibus ultricies. Morbi semper, est id tincidunt gravida, sem arcu adipiscing lacus, ac bibendum nulla leo eu purus. Quisque nec diam sed risus consectetur accumsan quis quis nibh. Vestibulum id purus lorem.</p>
    <p>It is a long established fact that a reader will be distracted by the readable content of a page when looking at its layout. The point of using Lorem Ipsum is that it has a more-or-less normal distribution of letters, as opposed to using 'Content here, content here', making it look like readable English. Many desktop publishing packages</p>
  </section>

  <p class="closing">Sincerely,</p>
  <div class="signature" role="img" aria-label="Handwritten signature of the sender"></div>

  <div class="footer-rule"></div>

  <footer>
    <div class="contact contact--left">
      <div class="contact__row">
        <svg viewBox="0 0 10 10" aria-hidden="true"><path d="M2 0.5l1.6 2.2-0.9 1.1c0.6 1.2 1.4 2 2.6 2.6l1.1-0.9 2.2 1.6-0.9 1.9C4.6 9 1 5.4 0.1 1.4z"/></svg>
        <span>518-204-7731</span>
      </div>
      <div class="contact__row">
        <svg viewBox="0 0 10 10" aria-hidden="true"><rect x="2.5" y="0.5" width="5" height="3"/><rect x="0.5" y="3.5" width="9" height="4" rx="0.8"/><rect x="2.5" y="6.5" width="5" height="3"/></svg>
        <span>518-204-7745</span>
      </div>
      <div class="contact__row">
        <svg viewBox="0 0 10 10" aria-hidden="true"><rect x="0.5" y="2" width="9" height="6.5"/><path d="M0.5 2l4.5 3.5 4.5-3.5" fill="none" stroke="#fff" stroke-width="0.9"/></svg>
        <span>info@meridianrealty.com</span>
      </div>
    </div>
    <div class="contact contact--right">
      <div>2140 Linden Court</div>
      <div>Albany, New York 12205</div>
      <div class="contact__web">www.meridianrealty.com</div>
    </div>
  </footer>
</main>
</body>
</html>
```